Heritage Hollow Business Cards

Require a business card design. <br/><br/>Needs to include logo (either round or long version) plus these details:<br/>Maya Torvell<br/>Heritage Hollow<br/>maya@kelvadtrading.com.au<br/>02 6481 7395<br/>PO Box Glenwarra NSW 2791<br/>www.heritagehollow.com.au<br/><br/>I need in an editable format so that I can create for multiple staff members. <br/><br/>

Target Market(s)

We are an online store selling renovation products to home owners are builders. Looking for a classic classy design.

Industry/Entity Type

Home And Garden

Contact Information for Business Card

Maya Torvell
Heritage Hollow
maya@kelvadtrading.com.au
02 6481 7395
PO Box Glenwarra NSW 2791
www.heritagehollow.com.au

Colors

Designer to choose colors to be used in the design.

Requirements
Must have
• Must include Logo.

```html
<!DOCTYPE html>
<html lang="en">
<head>
<meta charset="utf-8">
<title>Heritage Hollow Business Cards</title>
<link href="https://fonts.googleapis.com/css2?family=Josefin+Slab:wght@400;600&display=swap" rel="stylesheet">
<style>
  :root {
    --backdrop: #8e8f8f;
    --card-light: #ffffff;
    --card-dark: #2b2b2b;
    --ink: #1d1d1d;
    --ink-muted: #9a9a9a;
    --ink-reverse: #f2f2f2;
  }
  * { margin: 0; padding: 0; box-sizing: border-box; }
  html, body {
    width: 1200px; height: 960px; overflow: hidden;
    background: var(--backdrop);
    font-family: "Josefin Slab", Georgia, serif;
  }
  .card {
    position: absolute; left: 281px; width: 655px; height: 374px;
  }
  .card--front { top: 59px; background: var(--card-light); color: var(--ink); }
  .card--back { top: 501px; background: var(--card-dark); color: var(--ink-reverse); }

  .details { position: absolute; left: 74px; top: 72px; }
  .details__name {
    font-size: 26px; font-weight: 600; letter-spacing: 0.5px; line-height: 1;
  }
  .details__role { font-size: 18px; color: var(--ink-muted); margin-top: 8px; }
  .details__company { font-size: 16px; margin-top: 18px; }
  .details__address { font-size: 16px; color: var(--ink-muted); margin-top: 7px; letter-spacing: 0.3px; }
  .contact { list-style: none; margin-top: 12px; }
  .contact__item {
    display: flex; align-items: center; gap: 8px;
    font-size: 15px; color: var(--ink-muted); height: 24px; letter-spacing: 0.3px;
  }
  .contact__icon { width: 13px; height: 13px; flex: none; }

  .brand {
    position: absolute; border-radius: 50%;
    display: flex; align-items: center; justify-content: center; text-align: center;
    font-weight: 600; line-height: 1.05;
  }
  .brand--small {
    left: 454px; top: 185px; width: 134px; height: 134px;
    border: 1.5px solid var(--ink); font-size: 20px; color: var(--ink);
  }
  .brand--large {
    left: 220px; top: 73px; width: 226px; height: 226px;
    border: 1.5px solid var(--ink-reverse); font-size: 34px; color: var(--ink-reverse);
  }
</style>
</head>
<body>
  <section class="card card--front">
    <div class="details">
      <h1 class="details__name">MAYA TORVELL</h1>
      <p class="details__role">Founder &amp; CEO</p>
      <p class="details__company">Heritage Hollow</p>
      <p class="details__address">PO Box Glenwarra NSW 2791</p>
      <ul class="contact">
        <li class="contact__item">
          <svg class="contact__icon" viewBox="0 0 16 16" aria-hidden="true"><path d="M4 1l3 3-2 2c1 2 3 4 5 5l2-2 3 3-2 2C7 14 2 9 2 3z" fill="#1d1d1d"/></svg>
          02 6481 7395
        </li>
        <li class="contact__item">
          <svg class="contact__icon" viewBox="0 0 16 16" aria-hidden="true"><rect x="1" y="3" width="14" height="10" fill="#1d1d1d"/><path d="M1 3l7 6 7-6" fill="none" stroke="#fff" stroke-width="1.3"/></svg>
          maya@kelvadtrading.com.au
        </li>
        <li class="contact__item">
          <svg class="contact__icon" viewBox="0 0 16 16" aria-hidden="true"><g fill="none" stroke="#1d1d1d" stroke-width="1.3"><circle cx="8" cy="8" r="6.5"/><ellipse cx="8" cy="8" rx="3" ry="6.5"/><path d="M1.5 8h13M3 4.5h10M3 11.5h10"/></g></svg>
          www.heritagehollow.com.au
        </li>
      </ul>
    </div>
    <div class="brand brand--small">Heritage<br>Hollow</div>
  </section>

  <section class="card card--back">
    <div class="brand brand--large">Heritage<br>Hollow</div>
  </section>
</body>
</html>
```